Business card for law firm

Need business card for new law firm. Think confident, authoritative, conservative, but not stuffy or old-fashioned.

Contact Information for Business Card

Content for card - logo (uploaded), plus the following:

Paul Whitcombe (larger font)
Managing Partner (larger font, but not as large as name)
Level 9, 7 Ferris Lane
Sydney NSW 2000
Main Tel 02 9364 2710
Direct Tel 02 8472 3159
Email paul@qvlegal.com.au
www.qvlegal.com.au

Letterhead design should include logo plus:
Level 9, 7 Ferris Lane
Sydney NSW 2000
Tel 02 8472 3159
www.qvlegal.com.au

```html
<!DOCTYPE html>
<html lang="en">
<head>
<meta charset="utf-8">
<title>Quayvale Legal – Business Card</title>
<link rel="stylesheet" href="https://fonts.googleapis.com/css2?family=Open+Sans:wght@400;600;700&display=swap">
<style>
  :root {
    --navy: #001a57;
    --ink: #1a1a1a;
    --paper: #ffffff;
    --backdrop: #d9dadc;
    --rule: #b9bcc4;
  }
  * { box-sizing: border-box; margin: 0; padding: 0; }
  html, body {
    width: 1200px; height: 1112px; overflow: hidden;
    background: var(--backdrop);
    font-family: "Open Sans", Arial, sans-serif;
  }
  .stage { position: relative; width: 1200px; height: 1112px; }

  .card {
    position: absolute;
    width: 762px; height: 436px;
    border-radius: 28px;
    overflow: hidden;
  }
  .card--front { left: 358px; top: 86px; background: var(--paper); border: 1px solid #c4c6cb; }
  .card--back  { left: 72px;  top: 585px; background: var(--navy); }

  .footer-band {
    position: absolute; left: 0; right: 0; bottom: 0;
    height: 84px;
    background: var(--navy);
  }

  .firm-name {
    position: absolute;
    text-align: center;
    font-weight: 600;
    line-height: 1;
  }
  .firm-name__main { display: block; font-size: 46px; letter-spacing: 2px; }
  .firm-name__sub  { display: block; font-size: 18px; letter-spacing: 22px; margin-top: 16px; padding-left: 22px; }
  .card--front .firm-name { left: 40px; top: 200px; width: 380px; color: var(--navy); }
  .card--back  .firm-name { left: 30px; top: 62px;  width: 370px; color: var(--paper); }

  .divider {
    position: absolute; left: 432px; top: 72px;
    width: 1px; height: 200px; background: var(--rule);
  }
  .contact {
    position: absolute; left: 459px; top: 70px;
    color: var(--ink); font-size: 20px; line-height: 31px;
    list-style: none;
  }
  .contact__address { margin-bottom: 12px; }
  .contact__item { display: flex; align-items: center; gap: 7px; height: 34px; font-size: 20px; }
  .contact__item svg { width: 18px; height: 18px; flex: none; }

  .person {
    position: absolute; left: 440px; bottom: 16px; width: 320px;
    text-align: center; color: var(--paper);
  }
  .person__name { font-size: 23px; font-weight: 700; letter-spacing: 0.3px; line-height: 1.3; }
  .person__role { font-size: 17px; font-weight: 400; margin-top: 2px; letter-spacing: 0.3px; line-height: 1.3; }

  .web-address {
    position: absolute; right: 72px; bottom: 36px;
    color: var(--paper); font-size: 24px; letter-spacing: 4px;
  }
  .web-address b { font-weight: 700; }
</style>
</head>
<body>
<main class="stage">

  <section class="card card--front" aria-label="Business card front">
    <div class="footer-band" role="img" aria-label="Decorative navy and black wave band along the bottom edge"></div>

    <h1 class="firm-name">
      <span class="firm-name__main">QUAYVALE</span>
      <span class="firm-name__sub">LEGAL</span>
    </h1>

    <div class="divider"></div>

    <ul class="contact">
      <li class="contact__address">Level 9, 7 Ferris Lane<br>Sydney NSW 2000</li>
      <li class="contact__item">
        <svg viewBox="0 0 18 18"><circle cx="9" cy="9" r="8" fill="none" stroke="var(--navy)" stroke-width="1.6"/><path d="M6.5 4.5l2 1.5-1 1.6c.5 1.3 1.3 2.2 2.6 2.8l1.4-1 1.6 2-1.3 1.5C8.6 12.6 5.6 9.6 5.2 6z" fill="var(--navy)"/></svg>
        02 9364 2710(Main)
      </li>
      <li class="contact__item">
        <svg viewBox="0 0 18 18"><circle cx="9" cy="9" r="8" fill="none" stroke="var(--navy)" stroke-width="1.6"/><path d="M6.5 4.5l2 1.5-1 1.6c.5 1.3 1.3 2.2 2.6 2.8l1.4-1 1.6 2-1.3 1.5C8.6 12.6 5.6 9.6 5.2 6z" fill="var(--navy)"/></svg>
        02 8472 3159(Direct)
      </li>
      <li class="contact__item">
        <svg viewBox="0 0 18 18"><rect x="1" y="4" width="16" height="11" fill="var(--navy)"/><path d="M1.5 4.5L9 10l7.5-5.5" fill="none" stroke="#fff" stroke-width="1.4"/></svg>
        paul@qvlegal.com.au
      </li>
      <li class="contact__item">
        <svg viewBox="0 0 18 18" fill="none" stroke="var(--navy)" stroke-width="1.3"><circle cx="9" cy="9" r="7.5"/><ellipse cx="9" cy="9" rx="3.3" ry="7.5"/><path d="M1.5 9h15M3 5h12M3 13h12"/></svg>
        www.qvlegal.com.au
      </li>
    </ul>

    <div class="person">
      <p class="person__name">PAUL WHITCOMBE</p>
      <p class="person__role">MANAGING PARTNER</p>
    </div>
  </section>

  <section class="card card--back" aria-label="Business card back">
    <h2 class="firm-name">
      <span class="firm-name__main">QUAYVALE</span>
      <span class="firm-name__sub">LEGAL</span>
    </h2>
    <p class="web-address">www.<b>qvlegal</b>.com.au</p>
  </section>

</main>
</body>
</html>
```